Industry automation wholesale website

www.velturo.eu provides solutions for automation, building automation and digital signage.

Our products are rugged, reliable, energy saving and representative.

Scope of pages:
● welcome page
- scope of products
- applications, success stories and news
● category page
- short introduction
- sub categories
- product highlights
● product page
- short introduction
- about 3 to 4 pictures
- technical specifications: materials, dimensions
- price
- related products

Optional:
● contact page
- address
- contact form
● blog
- picture
- text
● logo
● favicon / apple touch icon

Conclusion:
● We need a professionally looking site
● Bright colors (e.g. white, grey, metalic colors, blue)

some pages we like:
http://www.prandek.de/
http://www.morvalix.de/

Target Market(s)

Our target market is the industrial sector
● Target audience: engineering and IT professionals

Industry/Entity Type

Building

Requirements
Must have
• ● only use free available fonts e.g. Lumara Type Library (http://www.lumaratype.com/webfonts)
Should not have
• ● sound
● flash

```html
<!DOCTYPE html>
<html lang="en">
<head>
<meta charset="utf-8">
<title>velturo – automation solutions</title>
<link href="https://fonts.googleapis.com/css2?family=Open+Sans:wght@300;400;600&family=Roboto:wght@300;400&display=swap" rel="stylesheet">
<style>
:root{
  --blue:#1a6e9c;
  --link:#2a8cc0;
  --ink:#333;
  --grey:#8a8a8a;
  --light:#b5b5b5;
  --line:#e4e4e4;
  --band:#f5f5f5;
  --green:#7ab51d;
  --green-dark:#5f9512;
  --tweet:#2aa3d6;
  --footer:#3f3f3f;
  --footer-deep:#2e2e2e;
  --footer-text:#a9a9a9;
}
*{margin:0;padding:0;box-sizing:border-box}
html,body{width:846px;height:1200px;overflow:hidden;background:#fff}
body{position:relative;font-family:"Open Sans",Arial,sans-serif;color:var(--ink)}
.abs{position:absolute}
.topline{left:0;top:0;width:846px;height:3px;background:#333}
.corner{right:0;top:0;width:0;height:0;border-top:26px solid #333;border-left:26px solid transparent}
.corner-plus{right:3px;top:-1px;color:#fff;font-size:11px;font-weight:600}
.topbar{left:0;top:3px;width:846px;height:29px;border-bottom:1px solid var(--line)}
.topbar-contact{left:73px;top:12px;font-size:7.5px;color:var(--light)}
.social{display:flex;gap:17px}
.social span{width:12px;height:12px;border-radius:50%;background:#9a9a9a;display:block}
.social-top{left:574px;top:11px}
.brand{display:flex;align-items:center;gap:8px}
.brand-name{font-family:"Open Sans",Arial,sans-serif;font-weight:400;color:var(--blue);font-size:31px;line-height:1;letter-spacing:-.5px}
.brand-dot{width:10px;height:10px;background:var(--blue);border-radius:50%}
.header-brand{left:72px;top:48px}
.nav{top:59px;font-size:12px;color:#555}
.nav.active{color:var(--blue)}
.nav-underline{left:418px;top:93px;width:36px;height:2px;background:var(--link)}
.hero{left:0;top:99px;width:846px;height:291px;background:linear-gradient(90deg,#eef1f3 0%,#f7f8f9 40%,#e9edf1 100%)}
.hero-photo{left:478px;top:16px;width:292px;height:275px;background:radial-gradient(ellipse at 50% 85%,#b9d3ea 0%,#d6e3ee 45%,rgba(230,236,241,0) 75%)}
.hero-title{left:72px;top:66px;font-size:21px;color:var(--blue);font-weight:400}
.hero-sub{left:71px;top:94px;font-size:14px;color:#222;font-weight:400}
.hero-text{left:67px;top:128px;width:340px;font-size:10.4px;line-height:18px;color:var(--grey);font-weight:300}
.btn-more{left:75px;top:189px;width:137px;height:27px;background:linear-gradient(#8cc62a,var(--green));border:1px solid var(--green-dark);color:#fff;font-weight:600;font-size:13px;text-align:center;line-height:25px}
.slide-arrow{top:104px;width:24px;height:46px;background:#eee;border:1px solid #ccc}
.slide-arrow svg{position:absolute;left:6px;top:14px}
.feature{top:415px;width:210px}
.feature-icon{position:absolute;left:0;top:4px;width:30px;height:22px;background:linear-gradient(135deg,#5a7fa3,#c8d3dc)}
.feature-title{margin-left:36px;font-size:10px;color:#222;line-height:13.5px;min-height:27px;display:flex;align-items:center}
.feature-text{margin-left:36px;margin-top:4px;width:172px;font-size:9px;color:var(--grey);line-height:16.5px;font-weight:300}
.feature-link{margin-left:36px;margin-top:7px;font-size:9px;color:var(--link)}
.welcome{left:0;top:524px;width:846px;height:126px;background:var(--band)}
.welcome-head{left:76px;top:20px;width:691px;height:30px;background:#fff;text-align:center;font-size:20px;color:var(--blue);line-height:30px;font-weight:400}
.welcome-text{left:80px;top:57px;width:686px;text-align:center;font-family:"Roboto",Arial,sans-serif;font-weight:300;font-size:14px;line-height:21px;color:var(--grey)}
.section-head{font-size:14px;color:#333;font-weight:400}
.rule{height:1px;background:var(--line)}
.quote{left:80px;width:337px;border:1px solid var(--line);background:#fff;padding:16px 15px;font-size:9px;line-height:16.5px;color:var(--light);font-weight:300}
.quote-tail{position:absolute;left:24px;bottom:-9px;width:14px;height:14px;background:#fff;border-left:1px solid var(--line);border-bottom:1px solid var(--line);transform:skewY(-40deg)}
.quote-name{left:120px;font-size:9px;color:#cfcfcf;font-weight:300}
.signup{left:436px;top:686px;width:337px;height:206px;background:var(--band)}
.signup-text{left:22px;top:24px;width:300px;font-size:9px;line-height:16.5px;color:#777;font-weight:300}
.field{left:22px;width:292px;height:27px;background:#fff;border:1px solid #d8d8d8;font-size:9px;color:#bbb;padding-left:8px;line-height:25px;font-weight:300}
.send{left:22px;top:150px;width:58px;height:33px;background:#fff;border:1px solid #d0d0d0;font-size:9.5px;text-align:center;line-height:31px}
.tweet{left:0;top:892px;width:846px;height:38px;background:var(--tweet);color:#fff;font-size:9.5px;line-height:38px;padding-left:95px;font-weight:300}
.tweet-bird{left:74px;top:906px;width:11px;height:9px;background:#fff;border-radius:50%}
.footer{left:0;top:930px;width:846px;height:232px;background:var(--footer)}
.footer .brand-name{color:#fff;font-size:27px}
.footer .brand-dot{background:#fff}
.footer-about{left:73px;top:84px;width:170px;font-size:9.5px;line-height:16.5px;color:var(--footer-text);font-weight:300}
.footer-head{top:48px;font-size:12px;color:#fff;font-weight:400;padding-bottom:7px;border-bottom:1px solid #555;width:165px}
.thumb{width:49px;height:49px;border:3px solid #2d2d2d}
.posts{left:430px;top:84px;font-size:9px;line-height:18.2px;color:var(--footer-text);font-weight:300;list-style:none}
.posts li::before{content:"›";margin-right:5px}
.contact{left:609px;top:78px;font-size:8.5px;line-height:23.5px;color:#ddd}
.bottombar{left:0;top:1162px;width:846px;height:38px;background:var(--footer-deep)}
.copyright{left:72px;top:13px;font-size:8.5px;color:#ddd}
.social-bottom{left:574px;top:15px}
.social-bottom span{background:#777}
</style>
</head>
<body>
<div class="abs topline"></div>
<div class="abs topbar"></div>
<div class="abs topbar-contact">Call Us: (1)555 010 482 - Mail: info@example.com</div>
<div class="abs social social-top" aria-label="Social links"><span></span><span></span><span></span><span></span><span></span><span></span><span></span></div>
<div class="abs corner"></div><div class="abs corner-plus">+</div>

<div class="abs header-brand">
  <div class="brand"><span class="brand-name">velturo</span><span class="brand-dot"></span></div>
</div>
<div class="abs nav active" style="left:421px">Home</div>
<div class="abs nav-underline"></div>
<div class="abs nav" style="left:483px">Products</div>
<div class="abs nav" style="left:551px">Contact</div>
<div class="abs nav" style="left:620px">Shopping Cart</div>
<svg class="abs" style="left:726px;top:58px" width="14" height="13" viewBox="0 0 14 13" fill="none" stroke="#bbb" stroke-width="1.3"><path d="M1 1h2l2 8h7l1.5-6H4"/><circle cx="6" cy="11.5" r="1"/><circle cx="11" cy="11.5" r="1"/></svg>
<svg class="abs" style="left:754px;top:58px" width="12" height="12" viewBox="0 0 12 12" fill="none" stroke="#bbb" stroke-width="1.4"><circle cx="5" cy="5" r="3.8"/><path d="M8 8l3.5 3.5"/></svg>

<section class="abs hero">
  <div class="abs hero-photo" role="img" aria-label="Photo of a smiling engineer in a light blue shirt, arms crossed"></div>
  <h1 class="abs hero-title">Touch Panel PC / Bedienterminal</h1>
  <h2 class="abs hero-sub">Industrial IP65 Front 24/7 Continuous Operation</h2>
  <p class="abs hero-text">Nexora is an ultra responsive &amp; highly customizable Presslane Theme for creative professionals and companies. Create powerful and stunning Websites out of the box.</p>
  <div class="abs btn-more">Read More...</div>
  <div class="abs slide-arrow" style="left:0"><svg width="10" height="18" viewBox="0 0 10 18" fill="none" stroke="#999" stroke-width="1.5"><path d="M8 1L2 9l6 8"/></svg></div>
  <div class="abs slide-arrow" style="left:821px"><svg width="10" height="18" viewBox="0 0 10 18" fill="none" stroke="#999" stroke-width="1.5"><path d="M2 1l6 8-6 8"/></svg></div>
</section>

<div class="abs feature" style="left:72px">
  <div class="feature-icon" role="img" aria-label="Product photo of remote IO modules"></div>
  <div class="feature-title">Modbus RTU / RS485<br>Remote IO Modules</div>
  <p class="feature-text">Asunt in anim uis aute irure dolor in reprehenderit in voluptate velit esse cillum dolore eu fugiat nulla pariatur.</p>
  <div class="feature-link">Take a Tour →</div>
</div>
<div class="abs feature" style="left:310px">
  <div class="feature-icon" role="img" aria-label="Product photo of a touch panel computer"></div>
  <div class="feature-title">Touch Panel Industry Computer</div>
  <p class="feature-text">Asunt in anim uis aute irure dolor in reprehenderit in voluptate velit esse cillum dolore eu fugiat nulla pariatur.</p>
  <div class="feature-link">Take a Tour →</div>
</div>
<div class="abs feature" style="left:549px">
  <div class="feature-icon" role="img" aria-label="Product photo of an embedded system box"></div>
  <div class="feature-title">Embedded systems for<br>industrial automation</div>
  <p class="feature-text">Asunt in anim uis aute irure dolor in reprehenderit in voluptate velit esse cillum dolore eu fugiat nulla pariatur.</p>
  <div class="feature-link">Take a Tour →</div>
</div>

<section class="abs welcome">
  <h2 class="abs welcome-head">Welcome to velturo analog digital measurements!</h2>
  <p class="abs welcome-text">Nexora is an ultra responsive, retina-ready Presslane Theme that everybody wants. It’s an incredible premium theme with powerful customization settings that helps you transform Nexora into your unique business tool.</p>
</section>

<h3 class="abs section-head" style="left:73px;top:649px">Testimonials</h3>
<div class="abs rule" style="left:73px;top:670px;width:337px"></div>
<div class="abs quote" style="top:683px;height:81px">Lorem ipsum dolor sit amet, consetetur sadipscing elitr, sed diam nonumy eirmod tempor invidunt ut labore et dolore magna aliquyam erat, sed diam voluptua.<div class="quote-tail"></div></div>
<div class="abs quote-name" style="top:769px">John Doe, Brightway Inc.</div>
<div class="abs quote" style="top:798px;height:64px">Lorem ipsum dolor sit amet, consetetur sadipscing elitr, sed diam nonumy eirmod tempor invidunt ut labore et dolore magna.<div class="quote-tail"></div></div>
<div class="abs quote-name" style="top:867px">Jane Miller, Company Inc.</div>

<h3 class="abs section-head" style="left:436px;top:647px">Join the Revolution</h3>
<div class="abs rule" style="left:436px;top:670px;width:337px"></div>
<form class="abs signup">
  <p class="abs signup-text">Lorem ipsum dolor sit amet, consetetur sadipscing elitr, sed diam nonumy eirmod tempor invidunt ut labore et dolore magna</p>
  <div class="abs field" style="top:66px">Your Name</div>
  <div class="abs field" style="top:108px">Your E-Mail</div>
  <div class="abs send">Send</div>
</form>

<div class="abs tweet">Did you already check out the brand new version of Nexora? It's definitely worth a look marketdepot.net/item/nexora-r...</div>
<div class="abs tweet-bird"></div>

<footer class="abs footer">
  <div class="abs" style="left:73px;top:46px">
    <div class="brand"><span class="brand-name">velturo</span><span class="brand-dot"></span></div>
  </div>
  <p class="abs footer-about">Aliquam fringilla, sapien egetferas scelerisque placerat, lorem libero cursus lorem, sed sodales lorem libero eu sapien. Nunc mattis feugiat justo vel faucibus. Nulla consequat feugiat malesuada.</p>
  <h4 class="abs footer-head" style="left:252px">Latest Projects</h4>
  <div class="abs thumb" style="left:252px;top:82px;background:linear-gradient(135deg,#d9b36a,#4a7ea8)" role="img" aria-label="Project image"></div>
  <div class="abs thumb" style="left:309px;top:82px;background:linear-gradient(135deg,#7aa6c8,#e6eef4)" role="img" aria-label="Project image"></div>
  <div class="abs thumb" style="left:365px;top:82px;background:linear-gradient(135deg,#6d6d6d,#c9c9c9)" role="img" aria-label="Project image"></div>
  <div class="abs thumb" style="left:252px;top:139px;background:linear-gradient(135deg,#e38a4a,#4f98c4)" role="img" aria-label="Project image"></div>
  <div class="abs thumb" style="left:309px;top:139px;background:linear-gradient(135deg,#5b86c2,#c27a8a)" role="img" aria-label="Project image"></div>
  <div class="abs thumb" style="left:365px;top:139px;background:linear-gradient(135deg,#a5b8c8,#6f5a3e)" role="img" aria-label="Project image"></div>
  <h4 class="abs footer-head" style="left:430px">Recent Posts</h4>
  <ul class="abs posts">
    <li>This is a Standard Post</li>
    <li>Post with Featured Image</li>
    <li>Beautiful Gallery Post</li>
    <li>This is a Video Post</li>
    <li>This is an Audio Post</li>
  </ul>
  <h4 class="abs footer-head" style="left:609px">Contact Info</h4>
  <div class="abs contact">Phone : +49-211-5550192<br>E-Mail : info@velturo.de<br>Web : http://www.velturo.de</div>
</footer>
<div class="abs bottombar">
  <div class="abs copyright">Copyright 2013 @www.velturo.eu.en</div>
  <div class="abs social social-bottom"><span></span><span></span><span></span><span></span><span></span><span></span><span></span></div>
</div>
</body>
</html>
```